Quarrybend Marble & Tile Needs a Business Card

Attached you will find your logo, my photo and design guidelines for a new business card. The final design will need two separate files to create an embossed card. The cards will be printed by www.plinkprint.com (Instructions below)
Format is the Plink SQUARE card
Quarrybend Marble And Tile is a brick and mortar, retail stone and tile shop.
One the front:
Quarrybend Marble And Tile
Dorian Fesslock
Owner
24807 Hollis Verdant Blvd
Suite P & R
Charlotte, NC 28193
Cell: 704-583-7142
Web: www.QuarrybendMarbleAndTile.com
(Make each word of the domain a different or alternating color)
On the back;
Something that shows beautiful colorful tile
Follow the design guide closely please. For more information see this page that describes creating the spot gloss file: https://www.plinkprint.com/us/business-cards/design-guidelines-spot-gloss
The logo is what we would like to have raised spot glossed.
Format is the Plink SQUARE card. See attahced guidlines.

```html
<!DOCTYPE html>
<html lang="en">
<head>
<meta charset="utf-8">
<title>Quarrybend Marble &amp; Tile – Business Card</title>
<link rel="stylesheet" href="https://fonts.googleapis.com/css2?family=Cinzel:wght@500&family=Carlito&display=swap">
<style>
  :root {
    --page-bg: #b7b7b7;
    --navy: #22323c;
    --navy-soft: #2c4250;
    --gold: #b07a2a;
    --accent: #d08a2a;
    --paper: #ffffff;
    --brand-faint: #2f6f93;
  }
  * { box-sizing: border-box; margin: 0; padding: 0; }
  html, body { width: 1200px; height: 995px; overflow: hidden; background: var(--page-bg); }
  .card {
    position: absolute;
    top: 296px;
    width: 401px;
    height: 402px;
    overflow: hidden;
  }
  .card-back { left: 192px; background: var(--navy); }
  .card-front { left: 607px; background: var(--paper); }
  .gold-rule {
    position: absolute;
    left: 0; right: 0;
    top: 366px;
    height: 3px;
    background: var(--gold);
  }
  .brand-name {
    position: absolute;
    font-family: "Cinzel", serif;
    font-weight: 500;
    letter-spacing: 0.12em;
    line-height: 1.2;
  }
  .card-back .brand-name {
    left: 110px; right: 24px; top: 160px;
    text-align: center;
    font-size: 22px;
    color: var(--brand-faint);
  }
  .card-front .brand-mark {
    position: absolute;
    left: 40px; top: 66px;
    width: 56px; height: 56px;
    background: var(--gold);
  }
  .card-front .brand-name {
    left: 146px; top: 68px;
    font-size: 23px;
    color: var(--navy);
  }
  .portrait {
    position: absolute;
    left: 22px; top: 188px;
    width: 123px; height: 162px;
    border-radius: 42px 0 42px 0;
    background: linear-gradient(160deg, var(--navy-soft), var(--navy));
  }
  .contact {
    position: absolute;
    left: 163px; top: 186px;
    right: 20px;
    font-family: "Carlito", sans-serif;
    color: var(--navy);
  }
  .contact-name {
    font-family: "Cinzel", serif;
    font-weight: 500;
    font-size: 19px;
    letter-spacing: 0.02em;
    line-height: 1.2;
  }
  .contact-role { font-size: 15px; color: var(--accent); line-height: 1.1; }
  .divider { width: 27px; height: 1px; background: var(--navy); margin: 10px 0 8px 2px; }
  .contact-line { font-size: 14px; line-height: 21px; white-space: nowrap; }
  .domain-word { color: var(--accent); }
</style>
</head>
<body>
  <section class="card card-back">
    <p class="brand-name">Quarrybend<br>Marble &amp; Tile</p>
    <div class="gold-rule"></div>
  </section>

  <section class="card card-front">
    <div class="brand-mark"></div>
    <p class="brand-name">Quarrybend<br>Marble &amp; Tile</p>

    <div class="portrait" role="img" aria-label="Portrait photo of the owner, Dorian Fesslock"></div>

    <div class="contact">
      <p class="contact-name">DORIAN FESSLOCK</p>
      <p class="contact-role">Owner</p>
      <div class="divider"></div>
      <p class="contact-line">704-583-7142</p>
      <p class="contact-line">www.<span class="domain-word">QuarrybendMarbleAndTile</span>.com</p>
      <div class="divider"></div>
      <p class="contact-line">24807 Hollis Verdant Blvd,</p>
      <p class="contact-line">Suite P &amp; R Charlotte, NC 28193</p>
    </div>

    <div class="gold-rule"></div>
  </section>
</body>
</html>
```